Vantro cards

I am in the auto motive, transportation business I would like a business card that is Something cool, modern edgy, having to do with car culture. I offer towing service for high and exotic cars. I also provide towing for collisions and car accidents. I offer open and enclosed transport nationwide.

Target Market(s)

Car culture people high end auto collectors

Industry/Entity Type

Towing car carrier

Contact Information for Business Card

My company colors black yellow and silver

Font styles to use
Serif

```html
<!DOCTYPE html>
<html lang="en">
<head>
<meta charset="utf-8">
<title>Vantro Transportation – Business Cards</title>
<link href="https://fonts.googleapis.com/css2?family=Arimo:wght@400;700&display=swap" rel="stylesheet">
<style>
  :root {
    --stage: #d9d9d6;
    --card: #222222;
    --yellow: #f7d83a;
    --white: #f2f2f2;
    --silver: #c4c4c4;
    --emboss: #2c2c2c;
  }
  * { box-sizing: border-box; margin: 0; padding: 0; }
  html, body {
    width: 1200px; height: 801px; overflow: hidden;
    background: var(--stage);
    font-family: "Arimo", Arial, sans-serif;
  }
  .stage {
    width: 1200px; height: 801px;
    display: flex; align-items: center; justify-content: center; gap: 40px;
  }
  .card {
    position: relative;
    width: 540px; height: 309px;
    background: var(--card);
    border-bottom: 4px solid var(--yellow);
    box-shadow: 0 10px 24px rgba(0,0,0,.25);
  }
  .brand {
    position: absolute; top: 52px; right: 40px;
    display: flex; align-items: center; gap: 10px;
  }
  .brand-mark { width: 16px; height: 16px; background: var(--yellow); }
  .brand-name {
    font-weight: 700; font-size: 38px; letter-spacing: 2px;
    color: var(--silver); text-transform: uppercase;
  }
  .divider {
    position: absolute; left: 32px; right: 18px; top: 158px;
    height: 1px; background: var(--yellow);
  }
  .person { position: absolute; left: 32px; top: 108px; }
  .person-name {
    font-weight: 700; font-size: 21px; color: var(--yellow);
    text-transform: uppercase; letter-spacing: .3px;
  }
  .person-role { font-size: 14px; color: var(--white); margin-top: 2px; }
  .contacts {
    position: absolute; left: 32px; top: 172px;
    list-style: none; display: grid; gap: 5px;
  }
  .contact {
    display: flex; align-items: center; gap: 9px;
    font-size: 14px; color: var(--white);
  }
  .contact-icon { width: 13px; height: 13px; flex: none; }
  .address {
    position: absolute; right: 36px; top: 182px;
    font-size: 13px; line-height: 1.45; color: var(--white);
  }
  .back-brand {
    position: absolute; inset: 0;
    display: flex; align-items: center; justify-content: center;
  }
  .back-brand .brand-name {
    font-size: 62px; color: var(--emboss);
    text-shadow: none;
  }
</style>
</head>
<body>
<main class="stage">
  <section class="card card-front" aria-label="Business card front">
    <div class="brand">
      <span class="brand-mark"></span>
      <span class="brand-name">Vantro</span>
    </div>
    <div class="person">
      <p class="person-name">Dorian Vale</p>
      <p class="person-role">CEO/Founder</p>
    </div>
    <div class="divider"></div>
    <ul class="contacts">
      <li class="contact">
        <svg class="contact-icon" viewBox="0 0 16 16" fill="var(--yellow)"><path d="M3 1l3 3-2 2c1 2 3 4 6 6l2-2 3 3-2 2C7 15 1 9 1 3z"/></svg>
        (555) 014 2280
      </li>
      <li class="contact">
        <svg class="contact-icon" viewBox="0 0 16 16" fill="none" stroke="var(--yellow)" stroke-width="2"><rect x="4" y="1" width="8" height="14" rx="1"/></svg>
        (555) 019 3317
      </li>
      <li class="contact">
        <svg class="contact-icon" viewBox="0 0 16 16" fill="var(--yellow)"><path d="M1 3h14v10H1z"/><path d="M1 3l7 6 7-6" stroke="var(--card)" stroke-width="1.4" fill="none"/></svg>
        info@vantrotransport.com
      </li>
      <li class="contact">
        <svg class="contact-icon" viewBox="0 0 16 16" fill="none" stroke="var(--yellow)" stroke-width="1.6"><circle cx="8" cy="8" r="6.5"/><path d="M1.5 8h13M8 1.5c-3 3-3 10 0 13M8 1.5c3 3 3 10 0 13"/></svg>
        www.vantrotransport.com
      </li>
    </ul>
    <address class="address" style="font-style:normal">
      P.O. Box 4781 Street<br>Country Name AB 3096
    </address>
  </section>

  <section class="card card-back" aria-label="Business card back">
    <div class="back-brand">
      <span class="brand-name">Vantro</span>
    </div>
  </section>
</main>
</body>
</html>
```